RW Framewell Inc Business cards

We need business cards using our existing logo but slightly modified. Right now the logo says RW Loadbearing Masonry. We want to keep the RW part of the design, but replace the Structural Concrete portion with "FRAMEWELL". Please see the attached file.
Ideally this would be a blank template so we can add Different Names, titles, and phone numbers later.
On the one side we want only the logo and on the other side the detail. I'm attaching an example for you to see.
Please reach out with any other questions. Our address and other details will be given out once we find a design we like.

Target Market(s)

Construction Industry

```html
<!DOCTYPE html>
<html lang="en">
<head>
<meta charset="utf-8">
<title>RW Framewell Inc – Business Cards</title>
<link rel="stylesheet" href="https://fonts.googleapis.com/css2?family=Montserrat:wght@500;600&family=Roboto:wght@400&display=swap">
<style>
  :root {
    --backdrop: #4b4b4d;
    --card: #1f2022;
    --card-edge: #2a2b2e;
    --brand-blue: #3b6fb6;
    --ink-light: #f2f2f2;
    --ink-soft: #d9d9d9;
  }
  * { box-sizing: border-box; margin: 0; padding: 0; }
  html, body {
    width: 799px; height: 1200px; overflow: hidden;
    background: var(--backdrop);
  }
  .sheet {
    position: relative; width: 799px; height: 1200px;
  }
  .card {
    position: absolute; left: 50px; width: 700px; height: 400px;
    background: var(--card);
    border: 1px solid var(--card-edge);
    border-radius: 6px;
    box-shadow: 0 12px 30px rgba(0,0,0,0.45);
  }
  .card--front { top: 100px; }
  .card--back  { top: 700px; }

  .wordmark {
    display: flex; align-items: center; gap: 14px;
    font-family: "Montserrat", sans-serif;
    font-weight: 600;
    color: var(--ink-light);
    letter-spacing: 0.12em;
    white-space: nowrap;
  }
  .wordmark__square {
    width: 22px; height: 22px; background: var(--brand-blue);
  }
  .card--front .wordmark {
    position: absolute; left: 50%; top: 50%;
    transform: translate(-50%, -50%);
    font-size: 40px;
  }
  .card--back .wordmark {
    position: absolute; left: 40px; top: 150px;
    font-size: 26px;
  }
  .card--back .wordmark__square { width: 18px; height: 18px; }

  .details {
    position: absolute; left: 390px; top: 110px;
    font-family: "Roboto", sans-serif;
    color: var(--ink-light);
  }
  .details__name {
    font-family: "Montserrat", sans-serif; font-weight: 500;
    font-size: 24px; color: var(--brand-blue);
  }
  .details__title {
    font-size: 15px; color: var(--ink-soft); margin-top: 2px; margin-bottom: 22px;
  }
  .contact-list { list-style: none; }
  .contact-list li {
    display: flex; align-items: center; gap: 10px;
    font-size: 16px; line-height: 26px;
  }
  .contact-list svg { width: 14px; height: 14px; fill: var(--brand-blue); flex: none; }
  .details__address {
    font-size: 16px; line-height: 22px; margin-top: 8px; font-style: normal;
  }
</style>
</head>
<body>
<main class="sheet">
  <section class="card card--front" aria-label="Card front">
    <div class="wordmark"><span class="wordmark__square"></span>RW FRAMEWELL</div>
  </section>

  <section class="card card--back" aria-label="Card back">
    <div class="wordmark"><span class="wordmark__square"></span>RW FRAMEWELL</div>
    <div class="details">
      <p class="details__name">Daniel RW Hart</p>
      <p class="details__title">Managing Director</p>
      <ul class="contact-list">
        <li>
          <svg viewBox="0 0 24 24" aria-hidden="true"><path d="M6.6 10.8a15 15 0 0 0 6.6 6.6l2.2-2.2c.3-.3.7-.4 1-.2 1.1.4 2.3.6 3.6.6.6 0 1 .4 1 1V20c0 .6-.4 1-1 1A17 17 0 0 1 3 4c0-.6.4-1 1-1h3.5c.6 0 1 .4 1 1 0 1.3.2 2.5.6 3.6.1.3 0 .7-.2 1z"/></svg>
          555-014-2288
        </li>
        <li>
          <svg viewBox="0 0 24 24" aria-hidden="true"><path d="M2 5h20v14H2z M2 5l10 8 10-8" fill="none" stroke="#3b6fb6" stroke-width="2"/></svg>
          daniel@framewellbuild.com
        </li>
        <li>
          <svg viewBox="0 0 24 24" aria-hidden="true"><circle cx="12" cy="12" r="9" fill="none" stroke="#3b6fb6" stroke-width="2"/><path d="M3 12h18M12 3c3 3 3 15 0 18M12 3c-3 3-3 15 0 18" fill="none" stroke="#3b6fb6" stroke-width="1.5"/></svg>
          www.framewellbuild.com
        </li>
      </ul>
      <address class="details__address">88 Beam Lane, Stoneford,<br>Oregon, US 97012</address>
    </div>
  </section>
</main>
</body>
</html>
```